Popular Golf Club needs attractive brochure

We need a brochure that will attract golfers to come to the Kestrel River area and the Brindlewood Golf Club for their golfing holiday. It also needs to address the availability of a function area and corporate functions in the clubhouse and corporate golf days on the course as well.
It will highlight our direct phone contact numbers and website as well.
We are a 36 Hole Championship Golf Course on the Kestrel River border of NSW and Victoria. 3 hours easy freeway drive from Melbourne. Over 300 sunny days every year. Fabulous golf weather all year round. Raincheck guarantee (if it rains we will give you free golf on you next visit).
The area is a golf and watersport playground. Sandy beaches, the mighty Kesterl River, home of the giant Kestrel Perch, fishing, camping, boating and golf all on your doorstep.
We can arrange Golf packages for individuals and groups including 3 and 4 star accommodation available all year round.

Target Market(s)

Golfers looking for holidays

Industry/Entity Type

Accommodation

Requirements
Must have
• Branding bar and logo. Colours signifying sun, grass and river.
Nice to have
• Smiling happy golfers, particularly more senior age group. Map of location and proximity to Melbourne. Photos of the course. some attached, many more available.

```html
<!DOCTYPE html>
<html lang="en">
<head>
<meta charset="utf-8">
<title>Brindlewood Golf Club – Brochure Front</title>
<link rel="stylesheet" href="https://fonts.googleapis.com/css2?family=Source+Sans+3:wght@400;600;700&family=Questrial&display=swap">
<style>
  :root {
    --page: #ece9e4;
    --paper: #ffffff;
    --ink: #1e1e1e;
    --grass: #8dc63f;
    --grass-dark: #7ab32f;
    --sun: #f4c21a;
    --river: #4fb8d0;
    --divider: #3a3a3a;
    --grey-text: #4a4a4a;
  }
  * { box-sizing: border-box; margin: 0; padding: 0; }
  html, body { width: 1200px; height: 979px; overflow: hidden; background: var(--page); }
  body { position: relative; font-family: "Source Sans 3", Arial, sans-serif; color: var(--ink); }

  .brochure {
    position: absolute; left: 39px; top: 89px; width: 1122px; height: 800px;
    background: var(--paper); overflow: hidden;
    box-shadow: 0 4px 18px rgba(0,0,0,.18);
  }
  .panel { position: absolute; top: 0; height: 638px; }
  .panel--about { left: 0; width: 374px; }
  .panel--visit { left: 374px; width: 374px; border-left: 1px solid var(--divider); border-right: 1px solid var(--divider); }
  .panel--contact { left: 748px; width: 374px; }

  .photo { position: absolute; left: 0; top: 0; width: 100%; }
  .photo--clubhouse {
    height: 210px;
    background:
      radial-gradient(ellipse 120px 18px at 62% 43%, rgba(255,236,190,.85), rgba(255,220,150,0) 100%),
      radial-gradient(ellipse 40px 14px at 20% 50%, rgba(255,240,200,.6), rgba(255,240,200,0) 100%),
      linear-gradient(180deg, #040506 0%, #07090b 30%, #141a14 44%, #2f4a20 52%, #3f5f28 62%, #1d2a14 80%, #0a0d08 100%);
  }
  .photo--bar {
    height: 290px;
    background:
      radial-gradient(ellipse 60px 140px at 22% 60%, rgba(220,224,228,.9), rgba(220,224,228,0) 100%),
      radial-gradient(ellipse 55px 120px at 45% 55%, rgba(120,110,95,.9), rgba(120,110,95,0) 100%),
      radial-gradient(ellipse 90px 110px at 76% 65%, rgba(214,170,70,.95), rgba(214,170,70,0) 100%),
      radial-gradient(ellipse 40px 90px at 60% 25%, rgba(60,62,66,.9), rgba(60,62,66,0) 100%),
      linear-gradient(180deg, #6a6e74 0%, #a9adb2 45%, #d2d4d6 80%, #b9bcbf 100%);
  }
  .photo--golfers {
    height: 306px;
    background:
      radial-gradient(ellipse 140px 60px at 70% 12%, rgba(220,230,210,.7), rgba(220,230,210,0) 100%),
      radial-gradient(ellipse 30px 70px at 22% 62%, rgba(255,255,255,.75), rgba(255,255,255,0) 100%),
      radial-gradient(ellipse 30px 70px at 45% 62%, rgba(240,240,235,.6), rgba(240,240,235,0) 100%),
      radial-gradient(ellipse 28px 70px at 60% 62%, rgba(90,190,140,.6), rgba(90,190,140,0) 100%),
      radial-gradient(ellipse 30px 80px at 86% 55%, rgba(250,250,240,.8), rgba(250,250,240,0) 100%),
      linear-gradient(180deg, #5f7a44 0%, #486636 35%, #5e8a35 58%, #79a640 74%, #dfeacf 90%, #ffffff 100%);
  }
  .map {
    position: absolute; left: 0; top: 438px; width: 100%; height: 200px;
    background:
      radial-gradient(ellipse 90px 70px at 58% 75%, rgba(190,220,170,.95), rgba(190,220,170,0) 100%),
      linear-gradient(100deg, rgba(255,255,255,0) 28%, rgba(250,215,120,.55) 30%, rgba(255,255,255,0) 32%),
      linear-gradient(160deg, #edebe7 0%, #e4e2de 60%, #dcdad5 100%);
  }

  .tagline {
    position: absolute; left: 14px; top: 146px;
    font-family: "Questrial", Arial, sans-serif; font-size: 15.5px; line-height: 19px;
    color: #fff; letter-spacing: .6px;
  }
  .intro {
    position: absolute; left: 20px; top: 230px; width: 338px;
    font-size: 12.4px; line-height: 16px; color: var(--ink);
  }
  .brand-mark {
    position: absolute; left: 0; width: 374px; top: 500px;
    display: flex; align-items: center; justify-content: center; gap: 10px;
    font-weight: 600; font-size: 20px; color: var(--grass-dark);
  }
  .brand-mark .dot { width: 44px; height: 44px; border-radius: 50%; background: var(--sun); }

  .web {
    position: absolute; left: 0; width: 100%; top: 341px; text-align: center;
    font-size: 19.5px; font-weight: 600; color: #111;
  }

  .quote {
    position: absolute; left: 14px; top: 160px; width: 345px;
    font-family: "Questrial", Arial, sans-serif; font-size: 15.5px; color: var(--sun);
    background: rgba(0,0,0,.45); padding: 3px 6px;
  }
  .club-name {
    position: absolute; left: 0; width: 100%; top: 350px;
    display: flex; align-items: center; justify-content: center; gap: 12px;
    font-size: 26px; letter-spacing: 3px; color: var(--grey-text);
  }
  .club-name .dot { width: 44px; height: 44px; border-radius: 50%; background: var(--river); }
  .cta {
    position: absolute; left: 82px; top: 476px; width: 209px; height: 45px;
    border-radius: 22px; background: linear-gradient(180deg, #a6d85a 0%, var(--grass) 55%, var(--grass-dark) 100%);
    color: #fff; font-weight: 700; font-size: 20px; line-height: 45px; text-align: center;
  }
  .phone {
    position: absolute; left: 0; width: 100%; top: 536px; text-align: center;
    font-size: 29px; color: var(--grass-dark); letter-spacing: .5px;
  }

  .waves { position: absolute; left: 0; top: 0; width: 1122px; height: 800px; }

  .footer { position: absolute; left: 0; top: 650px; width: 1122px; height: 150px; color: #fff; }
  .footer__web { position: absolute; left: 59px; top: 60px; font-size: 21.5px; }
  .footer__address { position: absolute; left: 380px; width: 360px; top: 34px; text-align: center; font-size: 13px; line-height: 19px; }
  .footer__address strong, .footer__people strong { font-weight: 700; }
  .footer__address .gap { display: block; height: 10px; }
  .footer__people { position: absolute; left: 806px; width: 262px; top: 20px; text-align: center; font-size: 13px; line-height: 17px; }
  .footer__people .gap { display: block; height: 6px; }
</style>
</head>
<body>
<main class="brochure">

  <section class="panel panel--about">
    <div class="photo photo--clubhouse" role="img" aria-label="Clubhouse lit up at night across the course"></div>
    <p class="tagline">36 Championship holes<br>Modern clubhouse and meals everyday!<br>Come play a round at your friendly Club</p>
    <p class="intro">"The secret is out! Along the Mighty Kestrel, Brindlewood Golf Course is maintained at the highest levels of excellence unsurpassed on the River. This magnificent 36 hole championship sand-belt course offers a challenge to golfers of all levels and hosts the annual Southern Pro Trainee Championships. Within excess of 300 days of sunshine each year, the regionboasts more sunny weather than the Gold Coast with two superb golf courses (President's and Captain's) that are suitable to play all year round.The courses abound with our native flora and fauna and water features are home to an amazing abundance of bird life. Kangaroos regularly frequent the lush fairways to graze and laze in the shade during the warmth of the after noon sun</p>
    <div class="brand-mark"><span class="dot"></span>Brindlewood</div>
  </section>

  <section class="panel panel--visit">
    <div class="photo photo--bar" role="img" aria-label="Row of beer taps at the clubhouse bar"></div>
    <p class="web">www.brindlewoodgolf.com.au</p>
    <div class="map" role="img" aria-label="Street map showing the club location in town"></div>
  </section>

  <section class="panel panel--contact">
    <div class="photo photo--golfers" role="img" aria-label="Group of golfers celebrating on the green"></div>
    <p class="quote">"A great golf course is just the beginning..."</p>
    <div class="club-name"><span class="dot"></span>BRINDLEWOOD</div>
    <div class="cta">Contact Us Today</div>
    <p class="phone">03 5550 1234</p>
  </section>

  <svg class="waves" viewBox="0 0 1122 800" aria-hidden="true">
    <path d="M0 586 C 250 600, 400 638, 600 644 C 800 648, 1000 632, 1122 624 L1122 640 C 1000 646, 800 658, 600 656 C 400 652, 250 616, 0 601 Z" fill="var(--river)"/>
    <path d="M0 636 C 200 644, 400 650, 560 652 L 560 657 C 400 657, 200 652, 0 648 Z" fill="var(--sun)"/>
    <path d="M700 640 C 850 630, 1000 606, 1122 586 L1122 601 C 1000 618, 850 642, 700 647 Z" fill="var(--sun)"/>
    <path d="M0 660 C 300 663, 700 663, 1122 644 L1122 800 L0 800 Z" fill="var(--grass)"/>
  </svg>

  <footer class="footer">
    <p class="footer__web">www.brindlewoodgolf.com.au</p>
    <p class="footer__address">
      <strong>Brindlewood Golf Club</strong><br>
      Harrow Road, PO Box 41, Brindlewood&nbsp; NSW&nbsp; 2790
      <span class="gap"></span>
      P: 03 5550 1234&nbsp;&nbsp; F: 03 5550 1235<br>
      <strong>FREECALL:</strong> 1800 555 017
    </p>
    <p class="footer__people">
      <strong>Club Email Address</strong><br>
      info@brindlewoodgolf.com.au
      <span class="gap"></span>
      <strong>Operations Manager - Carl Penfold</strong><br>
      om@brindlewoodgolf.com.au
      <span class="gap"></span>
      <strong>Chief Executive Officer - Mark Ellery</strong><br>
      ceo@brindlewoodgolf.com.au
    </p>
  </footer>

</main>
</body>
</html>
```